sydney wedding photography business needs a business card design

we need a business card design for a sydney based wedding photography and videography business. our business name is :golden hour studio and film. our target clients are 24-35 yrs female. our style is candid, organic, natural, dynamic. we are a team of young photographers and videographers, and help brides to create memories that they will cherish for the rest of their lives. the logo will be provided. we want an elegant design that reflects our style, and also want to give a great impression to our clients that we are one of the best studios in sydney and our brand means quality and premium service.

Target Market(s)

bride to be, 24-35 years old, living in sydney and surrunding areas

Industry/Entity Type

Wedding Photography

Contact Information for Business Card

address: 57 tarrant street, glenmore nsw 2047
mobile: 0431872259
phone: (02) 9163 2408
info@tidewillowstudio.net.au
www.tidewillowstudio.net.au
facebook:tidewillowweddings
instagram:tidewillowweddings

Font styles to use
Serif
Sans Serif

Requirements
Nice to have
• maybe add my slogan"memories beyond eternity" if the layout looks good
Should not have
• no black color, not good idea for wedding biz card

```html
<!DOCTYPE html>
<html lang="en">
<head>
<meta charset="utf-8">
<title>Golden Hour Studio and Film – Business Card</title>
<link rel="stylesheet" href="https://fonts.googleapis.com/css2?family=Jost:wght@300;400;500&display=swap">
<style>
  :root {
    --backdrop: #e9e4da;
    --card-dark: #3b2a1c;
    --card-dark-soft: #4d3826;
    --gold: #d9a21a;
    --gold-light: #e8b426;
    --gold-deep: #b7830f;
    --ink: #3a2716;
    --cream: #f5efe2;
  }
  * { margin: 0; padding: 0; box-sizing: border-box; }
  html, body { width: 1200px; height: 950px; overflow: hidden; }
  body {
    background: var(--backdrop);
    font-family: "Jost", sans-serif;
    position: relative;
  }
  .card {
    position: absolute;
    top: 320px;
    width: 540px;
    height: 310px;
    border-radius: 4px;
    overflow: hidden;
    box-shadow: 0 10px 28px rgba(0,0,0,.22);
  }

  /* Front */
  .card-front {
    left: 45px;
    background: linear-gradient(160deg, var(--card-dark-soft), var(--card-dark) 65%);
    color: var(--cream);
    border-bottom: 7px solid var(--gold);
  }
  .front-accent {
    position: absolute;
    left: 36px;
    top: 50px;
    width: 120px;
    height: 120px;
    border-radius: 50%;
    border: 16px solid rgba(217,162,26,.12);
  }
  .front-brand {
    position: absolute;
    right: 30px;
    top: 60px;
    width: 300px;
    text-align: right;
    color: var(--gold);
    font-weight: 400;
    font-size: 21px;
    letter-spacing: .5px;
    text-transform: lowercase;
  }
  .brand-rule {
    position: absolute;
    left: 232px;
    right: 24px;
    top: 118px;
    height: 1px;
    background: var(--gold);
  }
  .contact-list {
    position: absolute;
    list-style: none;
    font-weight: 300;
    font-size: 12.5px;
  }
  .contact-list li {
    display: flex;
    align-items: center;
    gap: 8px;
    margin-bottom: 8px;
    white-space: nowrap;
  }
  .contact-web { left: 232px; top: 134px; }
  .contact-phones { left: 232px; top: 212px; }
  .contact-list svg { width: 12px; height: 12px; flex: none; }
  .person {
    position: absolute;
    left: 30px;
    top: 192px;
  }
  .person-name {
    color: var(--gold);
    font-weight: 400;
    font-size: 17px;
    letter-spacing: 1px;
    text-transform: uppercase;
  }
  .person-role {
    font-size: 10.5px;
    letter-spacing: 1px;
    text-transform: uppercase;
    margin: 3px 0 9px;
  }
  .person-address {
    font-style: normal;
    font-weight: 300;
    font-size: 12.5px;
    line-height: 1.4;
  }
  .divider {
    position: absolute;
    left: 216px;
    top: 190px;
    width: 1px;
    height: 88px;
    background: var(--gold);
  }

  /* Back */
  .card-back {
    left: 615px;
    background: radial-gradient(ellipse at 35% 40%, var(--gold-light), var(--gold) 55%, var(--gold-deep));
    color: var(--ink);
  }
  .back-mark {
    position: absolute;
    left: 34px;
    top: 40px;
    display: flex;
    align-items: center;
    gap: 22px;
  }
  .back-mark-circle {
    width: 110px;
    height: 110px;
    border-radius: 50%;
    border: 14px solid var(--ink);
    flex: none;
  }
  .back-mark-name {
    font-weight: 500;
    font-size: 30px;
    line-height: 1.15;
    text-transform: lowercase;
    width: 300px;
  }
  .back-social {
    position: absolute;
    left: 34px;
    bottom: 36px;
    display: flex;
    align-items: center;
    gap: 8px;
    font-size: 13px;
    font-weight: 400;
  }
  .social-dot {
    width: 13px; height: 13px;
    border-radius: 50%;
    background: var(--ink);
  }
  .back-rule {
    position: absolute;
    left: 34px;
    right: 34px;
    bottom: 66px;
    height: 1px;
    background: var(--ink);
    opacity: .5;
  }
</style>
</head>
<body>
  <section class="card card-front" aria-label="Business card front">
    <div class="front-accent" aria-hidden="true"></div>
    <div class="front-brand">golden hour studio and film</div>
    <div class="brand-rule"></div>

    <ul class="contact-list contact-web">
      <li>
        <svg viewBox="0 0 12 12" aria-hidden="true"><path d="M1 3h10v6H1z M1 3l5 3.5L11 3" fill="none" stroke="#d9a21a" stroke-width="1.2"/></svg>
        info@tidewillowstudio.net.au
      </li>
      <li>
        <svg viewBox="0 0 12 12" aria-hidden="true"><circle cx="6" cy="6" r="5" fill="none" stroke="#d9a21a" stroke-width="1.2"/><path d="M1 6h10M6 1c2.5 3 2.5 7 0 10M6 1c-2.5 3-2.5 7 0 10" fill="none" stroke="#d9a21a" stroke-width="1"/></svg>
        www.tidewillowstudio.net.au
      </li>
    </ul>

    <div class="person">
      <div class="person-name">Mara Ellison</div>
      <div class="person-role">Photographer</div>
      <address class="person-address">57 tarrant street<br>glenmore nsw 2047</address>
    </div>
    <div class="divider"></div>

    <ul class="contact-list contact-phones">
      <li>
        <svg viewBox="0 0 12 12" aria-hidden="true"><path fill="#d9a21a" d="M2.5 1l2 2.5-1 1.2c.8 1.5 1.8 2.5 3.3 3.3l1.2-1 2.5 2-1 2C5 10.5 1.5 7 1 2.5z"/></svg>
        (02) 9163 2408
      </li>
      <li>
        <svg viewBox="0 0 12 12" aria-hidden="true"><rect x="3" y="0.5" width="6" height="11" rx="1" fill="none" stroke="#d9a21a" stroke-width="1.2"/><circle cx="6" cy="9.5" r=".8" fill="#d9a21a"/></svg>
        0431 872 259
      </li>
    </ul>
  </section>

  <section class="card card-back" aria-label="Business card back">
    <div class="back-mark">
      <span class="back-mark-circle" aria-hidden="true"></span>
      <div class="back-mark-name">golden hour studio and film</div>
    </div>
    <div class="back-rule"></div>
    <div class="back-social">
      <span class="social-dot" aria-hidden="true"></span>
      tidewillowweddings
    </div>
  </section>
</body>
</html>
```